Business Card Design for Brightlane

The company provides engineering tender consulting services and personnel resources. The target market is large engineering construction and services companies. The business is based in Australia.

```html
<!DOCTYPE html>
<html lang="en">
<head>
<meta charset="utf-8">
<title>Brightlane Business Card</title>
<link rel="stylesheet" href="https://fonts.googleapis.com/css2?family=Source+Sans+3:wght@400;700&display=swap">
<style>
  :root {
    --page: #ffffff;
    --card-white: #ffffff;
    --front-blue: #1565b8;
    --back-blue: #2d78c2;
    --brand-blue: #1a5fae;
    --mark-grey: #9a9a9a;
    --name-tint: #9ccbf2;
    --detail-tint: #c9e2f8;
    --link-blue: #2f6fb5;
    --card-edge: #e3e6ea;
  }
  * { box-sizing: border-box; margin: 0; padding: 0; }
  html, body {
    width: 1200px;
    height: 800px;
    overflow: hidden;
    background: var(--page);
    font-family: "Source Sans 3", "Myriad Pro", Arial, sans-serif;
  }
  .stage { position: relative; width: 1200px; height: 800px; }

  .card {
    position: absolute;
    width: 607px;
    height: 346px;
    overflow: hidden;
    background: var(--card-white);
    outline: 1px solid var(--card-edge);
  }
  .card--front { left: 80px; top: 111px; z-index: 2; }
  .card--back  { left: 493px; top: 349px; z-index: 1; }

  .card__wave { position: absolute; inset: 0; width: 100%; height: 100%; }

  .brand {
    position: absolute;
    left: 0; right: 0;
    display: flex;
    flex-direction: column;
    align-items: center;
    gap: 12px;
  }
  .brand__square { width: 26px; height: 26px; }
  .brand__name {
    font-weight: 700;
    font-size: 44px;
    line-height: 1;
    letter-spacing: -0.5px;
  }
  .card--front .brand { top: 62px; }
  .card--front .brand__square { background: var(--mark-grey); }
  .card--front .brand__name { color: var(--brand-blue); }
  .card--back .brand { top: 92px; }
  .card--back .brand__square { background: var(--card-white); }
  .card--back .brand__name { color: var(--card-white); }

  .holder-name {
    position: absolute;
    left: 24px;
    top: 198px;
    font-size: 21px;
    font-weight: 400;
    color: var(--name-tint);
    letter-spacing: 0.3px;
  }
  .contact {
    position: absolute;
    top: 262px;
    font-size: 13px;
    line-height: 21px;
    color: var(--detail-tint);
  }
  .contact--left { left: 24px; }
  .contact--right { right: 29px; top: 262px; text-align: right; }

  .back-url {
    position: absolute;
    left: 0; right: 0;
    top: 304px;
    text-align: center;
    font-size: 13px;
    color: var(--link-blue);
  }
</style>
</head>
<body>
<main class="stage">

  <section class="card card--front" aria-label="Card front">
    <svg class="card__wave" viewBox="0 0 600 340" preserveAspectRatio="none" aria-hidden="true">
      <path d="M0,168 C120,160 200,200 300,206 C420,212 520,172 600,142 L600,340 L0,340 Z" fill="var(--front-blue)"/>
      <path d="M230,196 C330,232 460,226 600,176" fill="none" stroke="var(--card-white)" stroke-width="4"/>
    </svg>
    <div class="brand">
      <span class="brand__square"></span>
      <span class="brand__name">Brightlane</span>
    </div>
    <p class="holder-name">YOUR NAME</p>
    <div class="contact contact--left">
      <p>000.000.0000</p>
      <p>info@brightlane.com</p>
      <p>www.brightlane.com</p>
    </div>
    <div class="contact contact--right">
      <p>000-b Harbour Lane, #00</p>
      <p>Port Avery, NSW 0000</p>
    </div>
  </section>

  <section class="card card--back" aria-label="Card back">
    <svg class="card__wave" viewBox="0 0 600 340" preserveAspectRatio="none" aria-hidden="true">
      <path d="M0,0 H600 V205 C500,238 400,254 300,248 C180,240 90,226 0,226 Z" fill="var(--back-blue)"/>
      <path d="M200,244 C330,276 470,270 600,230" fill="none" stroke="var(--back-blue)" stroke-width="4"/>
    </svg>
    <div class="brand">
      <span class="brand__square"></span>
      <span class="brand__name">Brightlane</span>
    </div>
    <p class="back-url">www.brightlanecom</p>
  </section>

</main>
</body>
</html>
```